Website for a Psychologist in Private Practice

I need a cool web design for my website: www.drkalvoric.com. I would like it to look professional. Keep all the current content and add: Space for video; radio spots (see Silver Cedar Tunes Logo below for those); Quick Inquiry; Friendora link; 5 star rating on Rivo; a map; reviews from former patients. I am open to suggestions.

Target Market(s)

Those seeking individual and marital counseling.

Industry/Entity Type

Mental Health

Number of Pages Required

1 page

Font styles to use
Sans Serif
Other font styles liked:
• I'm open but no hard to read script

Requirements
Must have
• All the content on my home page with link for video and radio spots. List services and degrees and expertices (pics not necessary).
Nice to have
• A video of me and radio conversations (logo of Silver Cedar Tunes radio attached).
Should not have
• Cartoons, comedy, etc.... I don't need pictures of services (marital, depression, etc...) Just list those.

```html
<!DOCTYPE html>
<html lang="en">
<head>
<meta charset="utf-8">
<title>Dr. Marla J. Kalvoric – Psychologist</title>
<link href="https://fonts.googleapis.com/css2?family=Cinzel:wght@400;700&family=Lato:ital,wght@0,400;0,700;1,400&display=swap" rel="stylesheet">
<style>
:root{
  --blue:#1f7fc4;
  --blue-band:#2f86c8;
  --green:#15960f;
  --green-dark:#0f7d0a;
  --ink:#222;
  --muted:#555;
  --rule:#cfcfcf;
  --panel:#f3f3f3;
  --footer-dark:#5a5a5a;
  --white:#fff;
}
*{box-sizing:border-box;margin:0;padding:0}
html,body{width:904px;height:1200px;overflow:hidden;background:var(--white)}
body{font-family:'Lato',sans-serif;color:var(--ink);position:relative}
.abs{position:absolute}
.heading{font-family:'Cinzel',serif;color:var(--blue);font-weight:400;font-size:20px;letter-spacing:.5px;white-space:nowrap}
.heading--compact{font-size:17.5px;letter-spacing:-.2px;top:866px}
.rule{position:absolute;height:1px;background:var(--rule)}

/* header */
.site-header{position:absolute;left:0;top:0;width:904px;height:72px;background:var(--white);border-top:2px solid var(--blue)}
.brand{left:58px;top:16px;font-family:'Cinzel',serif;font-size:33px;color:var(--blue);letter-spacing:.5px}
.schedule-tab{left:656px;top:0;width:204px;height:26px;background:var(--blue);clip-path:polygon(0 0,100% 0,95% 100%,4% 100%);color:var(--white);font-size:12px;font-weight:700;display:flex;align-items:center;justify-content:center;gap:8px}
.contact-line{top:42px;display:flex;align-items:center;gap:6px;font-size:12.5px;color:#333}
.dot-icon{width:20px;height:20px;border-radius:50%;background:var(--green);display:flex;align-items:center;justify-content:center}

/* nav */
.main-nav{position:absolute;left:0;top:72px;width:904px;height:33px;background:var(--green)}
.main-nav a{position:absolute;top:0;height:33px;display:flex;align-items:center;justify-content:center;color:var(--white);text-decoration:none;font-family:'Cinzel',serif;font-size:12.5px;letter-spacing:.6px;border-left:1px solid rgba(255,255,255,.25)}
.main-nav a.active{background:var(--blue);border-left:none}

/* hero */
.hero{left:0;top:105px;width:904px;height:345px;background:linear-gradient(180deg,#cfd9e3 0%,#b9c6cf 35%,#7f9468 62%,#5f7f3a 80%,#6f8a3c 100%)}
.hero-title{right:62px;top:118px;text-align:right;font-family:'Cinzel',serif;font-weight:700;font-size:30px;line-height:36px;color:var(--white);text-shadow:0 2px 6px rgba(0,0,0,.55)}
.hero-arrow{top:152px}

/* services */
.service{position:absolute;top:406px;width:120px;text-align:center}
.service .badge{width:96px;height:96px;margin:0 auto;border-radius:50%;border:5px solid var(--green);background:radial-gradient(circle at 50% 40%,#fff 0%,#eef3ee 70%,#d6e3d6 100%)}
.service .label{margin-top:10px;font-weight:700;font-size:14px;line-height:18px;color:#222}

/* about */
.about-band{left:0;top:574px;width:904px;height:264px;background:var(--panel)}
.about-text{left:61px;top:642px;width:486px;font-size:11.3px;line-height:18px;color:#222}
.degrees-title{left:62px;top:743px;font-family:'Cinzel',serif;font-size:17px;letter-spacing:.5px}
.check-list{list-style:none}
.check-list li{display:flex;align-items:center;gap:6px;height:21px;font-size:11.3px;color:#222}
.video-frame{left:585px;top:646px;width:258px;height:156px;background:linear-gradient(135deg,#d9dde0 0%,#c8bfb4 45%,#b59a86 70%,#e6e6e2 100%);box-shadow:0 6px 8px -4px rgba(0,0,0,.4)}
.video-controls{position:absolute;left:0;bottom:0;width:100%;height:22px;background:#222;display:flex;align-items:center;gap:8px;padding:0 8px}
.progress{flex:1;height:4px;background:#555;border-radius:2px;position:relative}
.progress span{position:absolute;left:0;top:0;height:4px;width:34%;background:#d12b2b;border-radius:2px}

/* sessions row */
.session-list{left:60px;top:914px;width:260px;display:grid;grid-template-columns:108px 152px;row-gap:6px;font-size:10.4px}
.session-list li{list-style:none;display:flex;align-items:center;gap:4px;height:20px}
.btn{position:absolute;background:var(--green);color:var(--white);font-size:10px;font-weight:700;letter-spacing:.4px;display:flex;align-items:center;justify-content:center;text-transform:uppercase}
.field{position:absolute;left:366px;width:196px;border:1px solid #999;background:var(--white);font-size:10px;color:#333;padding:5px 7px}
.quote-box{left:598px;top:920px;width:245px;height:100px;border:1px solid #ccc;border-radius:6px;background:var(--white);padding:12px 10px;font-style:italic;font-size:10px;line-height:17.5px;color:#222}
.quote-tail{left:690px;top:1018px}
.carousel-arrows{left:818px;top:871px}

/* footer */
.footer-band{left:0;top:1078px;width:904px;height:90px;background:var(--blue-band)}
.footer-nav a{position:absolute;top:1097px;color:var(--white);font-size:11px;text-decoration:none}
.footer-contact{position:absolute;top:1136px;display:flex;align-items:center;gap:6px;color:var(--white);font-size:12px}
.partner{position:absolute;top:1118px;width:77px;height:34px;background:var(--white)}
.footer-bottom{left:0;top:1168px;width:904px;height:32px;background:var(--footer-dark);color:#eee;font-size:10.5px}
.social{position:absolute;top:9px;display:flex;align-items:center;gap:4px;font-size:10px;color:#eee}
.social i{width:12px;height:12px;border:1px solid #eee;border-radius:50%;display:block}
</style>
</head>
<body>

<header class="site-header">
  <div class="abs brand">Dr. Marla J. Kalvoric</div>
  <div class="abs schedule-tab">
    <svg width="16" height="15" viewBox="0 0 16 15"><rect x="1" y="2" width="12" height="11" fill="none" stroke="#fff" stroke-width="1.3"/><line x1="1" y1="5.5" x2="13" y2="5.5" stroke="#fff"/><circle cx="12" cy="11" r="3.4" fill="#1f7fc4" stroke="#fff"/><path d="M12 9.4V11h1.3" stroke="#fff" fill="none"/></svg>
    Schedule An Appointment
  </div>
  <div class="abs contact-line" style="left:580px">
    <span class="dot-icon"><svg width="10" height="8" viewBox="0 0 10 8"><rect x=".5" y=".5" width="9" height="7" fill="#fff"/><path d="M.5 .5L5 4.5 9.5.5" stroke="#15960f" fill="none"/></svg></span>
    mk@drkalvoric.com
  </div>
  <div class="abs contact-line" style="left:727px">
    <span class="dot-icon"><svg width="10" height="10" viewBox="0 0 10 10"><path d="M2 1l2 2-1 1.3a6 6 0 0 0 2.7 2.7L7 6l2 2-1.3 1.5C4.5 9 1 5.5.5 2.3z" fill="#fff"/></svg></span>
    (555) 210 4837
  </div>
</header>

<nav class="main-nav">
  <a class="active" style="left:61px;width:70px">Home</a>
  <a style="left:131px;width:107px">Bio</a>
  <a style="left:238px;width:176px">My Expertise</a>
  <a style="left:414px;width:144px">Sessions</a>
  <a style="left:558px;width:159px">Resources</a>
  <a style="left:717px;width:187px">Contact Me</a>
</nav>

<section class="abs hero" role="img" aria-label="Photo of a woman with outstretched arms in a meadow facing green mountains under a cloudy sky">
  <h1 class="abs hero-title">Helping You To Find<br>Your Own Solutions</h1>
  <svg class="abs hero-arrow" style="left:22px" width="20" height="44" viewBox="0 0 20 44"><path d="M18 2L2 22l16 20" stroke="rgba(255,255,255,.6)" stroke-width="1.5" fill="none"/></svg>
  <svg class="abs hero-arrow" style="right:22px" width="20" height="44" viewBox="0 0 20 44"><path d="M2 2l16 20L2 42" stroke="rgba(255,255,255,.7)" stroke-width="1.5" fill="none"/></svg>
</section>

<section aria-label="Areas of expertise">
  <div class="service" style="left:49px"><div class="badge" role="img" aria-label="Dating illustration"></div><div class="label">Dating</div></div>
  <div class="service" style="left:185px"><div class="badge" role="img" aria-label="Marriage illustration"></div><div class="label">Marriage</div></div>
  <div class="service" style="left:322px"><div class="badge" role="img" aria-label="Professional relationship illustration"></div><div class="label">Professional<br>Relationship</div></div>
  <div class="service" style="left:458px"><div class="badge" role="img" aria-label="Depression and anxiety illustration"></div><div class="label">Depression &amp;<br>Anxiety Issues</div></div>
  <div class="service" style="left:594px"><div class="badge" role="img" aria-label="Personality disorders illustration"></div><div class="label">Personality<br>Disorders</div></div>
  <div class="service" style="left:730px"><div class="badge" role="img" aria-label="Life management illustration"></div><div class="label">Life<br>Management</div></div>
</section>

<section class="abs about-band" aria-label="About"></section>
<h2 class="abs heading" style="left:60px;top:598px">About Dr. Marla J. Kalvoric</h2>
<div class="rule" style="left:60px;top:633px;width:481px"></div>
<p class="abs about-text">Lorem ipsum dolor sit amet, consectetuer adipiscing elit, sed diam nonummy nibh euismod tincidunt ut laoreet dolore magna aliquam erat volutpat. Ut wisi enim ad minim veniam, quis nostrud exerci tation ullamcorper suscipit lobortis nisl ut aliquip ex ea commodo consequat.</p>
<div class="abs degrees-title">My Degrees</div>
<svg class="abs" style="left:172px;top:710px" width="34" height="90" viewBox="0 0 34 90"><path d="M4 2c14 0 14 8 14 20s2 20 12 23c-10 3-12 11-12 23s0 20-14 20" stroke="#222" stroke-width="3" fill="none"/></svg>
<ul class="abs check-list" style="left:211px;top:713px">
  <li><svg width="10" height="9" viewBox="0 0 10 9"><path d="M1 5l3 3 5-7" stroke="#15960f" stroke-width="2" fill="none"/></svg>Doctoral Degree in Clinical Psychology</li>
  <li><svg width="10" height="9" viewBox="0 0 10 9"><path d="M1 5l3 3 5-7" stroke="#15960f" stroke-width="2" fill="none"/></svg>Masters Degree in Counseling Psychology</li>
  <li><svg width="10" height="9" viewBox="0 0 10 9"><path d="M1 5l3 3 5-7" stroke="#15960f" stroke-width="2" fill="none"/></svg>Doctoral Internship, Westbrook Medical Center</li>
  <li><svg width="10" height="9" viewBox="0 0 10 9"><path d="M1 5l3 3 5-7" stroke="#15960f" stroke-width="2" fill="none"/></svg>Masters Internship, Alderway Clinic</li>
</ul>
<div class="abs" style="left:564px;top:600px;width:1px;height:210px;background:linear-gradient(180deg,transparent,#ddd,transparent)"></div>
<h2 class="abs heading" style="left:582px;top:598px">View Video</h2>
<div class="rule" style="left:582px;top:633px;width:262px"></div>
<div class="abs video-frame" role="img" aria-label="Video still of a counseling session with two women talking to a therapist">
  <div class="video-controls">
    <svg width="8" height="9" viewBox="0 0 8 9"><path d="M0 0l8 4.5L0 9z" fill="#fff"/></svg>
    <svg width="10" height="9" viewBox="0 0 10 9"><path d="M0 3h2l3-3v9L2 6H0z" fill="#ccc"/><path d="M7 2.5a3 3 0 0 1 0 4" stroke="#ccc" fill="none"/></svg>
    <div class="progress"><span></span></div>
    <svg width="10" height="10" viewBox="0 0 10 10"><path d="M6 1h3v3M4 9H1V6M9 1L6 4M1 9l3-3" stroke="#fff" fill="none"/></svg>
  </div>
</div>

<h2 class="abs heading" style="left:60px;top:864px">My Sessions</h2>
<div class="rule" style="left:60px;top:896px;width:248px"></div>
<ul class="abs session-list">
  <li><svg width="9" height="9" viewBox="0 0 10 9"><path d="M1 5l3 3 5-7" stroke="#111" stroke-width="2" fill="none"/></svg>Individual Sessions</li>
  <li><svg width="9" height="9" viewBox="0 0 10 9"><path d="M1 5l3 3 5-7" stroke="#111" stroke-width="2" fill="none"/></svg>Divorce Mediation</li>
  <li><svg width="9" height="9" viewBox="0 0 10 9"><path d="M1 5l3 3 5-7" stroke="#111" stroke-width="2" fill="none"/></svg>Marriage Sessions</li>
  <li><svg width="9" height="9" viewBox="0 0 10 9"><path d="M1 5l3 3 5-7" stroke="#111" stroke-width="2" fill="none"/></svg>Custody Evaluation Sessions</li>
  <li><svg width="9" height="9" viewBox="0 0 10 9"><path d="M1 5l3 3 5-7" stroke="#111" stroke-width="2" fill="none"/></svg>Family Sessions</li>
  <li><svg width="9" height="9" viewBox="0 0 10 9"><path d="M1 5l3 3 5-7" stroke="#111" stroke-width="2" fill="none"/></svg>Testing Sessions</li>
  <li><svg width="9" height="9" viewBox="0 0 10 9"><path d="M1 5l3 3 5-7" stroke="#111" stroke-width="2" fill="none"/></svg>Phone Sessions</li>
  <li><svg width="9" height="9" viewBox="0 0 10 9"><path d="M1 5l3 3 5-7" stroke="#111" stroke-width="2" fill="none"/></svg>Weekend / Holiday Sessions</li>
</ul>
<div class="btn" style="left:60px;top:1027px;width:75px;height:23px">Read More</div>

<h2 class="abs heading" style="left:366px;top:864px">Quick Inquiry</h2>
<div class="rule" style="left:366px;top:896px;width:197px"></div>
<div class="field" style="top:918px;height:23px">Name</div>
<div class="field" style="top:949px;height:23px">Email</div>
<div class="field" style="top:978px;height:40px">Message</div>
<div class="btn" style="left:367px;top:1026px;width:67px;height:22px">Submit</div>

<h2 class="abs heading heading--compact" style="left:595px">Radio Conversations</h2>
<svg class="abs carousel-arrows" width="26" height="12" viewBox="0 0 26 12"><path d="M6 1L1 6l5 5M20 1l5 5-5 5" stroke="#222" stroke-width="2" fill="none"/></svg>
<div class="rule" style="left:595px;top:896px;width:249px"></div>
<blockquote class="abs quote-box">Lorem ipsum dolor sit amet, consectetuer adipiscingelit, sed diam nonummy nibh euismod tinciduntttfgf dolore magna aliquam erat volutpat. tinciduntpsum dolor sit amet, consectetuer adip</blockquote>
<svg class="abs quote-tail" width="34" height="20" viewBox="0 0 34 20"><path d="M0 1h34L32 18z" fill="#fff"/><path d="M0 1L32 18 34 1" stroke="#ccc" fill="none"/></svg>
<div class="abs" style="right:60px;top:1025px;font-size:10.5px;font-weight:700;color:#333">- Lorem ipsum dolor</div>
<div class="abs" style="left:760px;top:1039px;font-size:9px;font-style:italic;color:var(--blue)">Sitamet, CA</div>

<footer>
  <div class="abs footer-band"></div>
  <nav class="footer-nav">
    <a style="left:62px">Home</a><a style="left:133px">Bio</a><a style="left:190px">My Expertise</a>
    <a style="left:304px">Sessions</a><a style="left:393px">Resources</a><a style="left:493px">Contact Me</a>
  </nav>
  <div class="abs" style="left:62px;top:1125px;width:568px;height:1px;background:rgba(255,255,255,.35)"></div>
  <div class="footer-contact" style="left:62px"><svg width="10" height="10" viewBox="0 0 10 10"><path d="M2 1l2 2-1 1.3a6 6 0 0 0 2.7 2.7L7 6l2 2-1.3 1.5C4.5 9 1 5.5.5 2.3z" fill="#fff"/></svg>(555) 210 4837</div>
  <div class="footer-contact" style="left:189px"><svg width="11" height="8" viewBox="0 0 10 8"><rect x=".5" y=".5" width="9" height="7" fill="#fff"/><path d="M.5 .5L5 4.5 9.5.5" stroke="#2f86c8" fill="none"/></svg>mk@drkalvoric.com</div>
  <div class="footer-contact" style="left:344px"><svg width="8" height="11" viewBox="0 0 8 11"><path d="M4 11S0 6 0 4a4 4 0 0 1 8 0c0 2-4 7-4 7z" fill="#fff"/><circle cx="4" cy="4" r="1.5" fill="#2f86c8"/></svg>410 Harbor Lane, Suite 120 Bayview, CA 90210</div>
  <div class="abs" style="right:60px;top:1097px;color:#fff;font-size:11px;font-weight:700">A portion of all revenue is donated to</div>
  <div class="partner" style="left:683px" role="img" aria-label="Partner charity badge"></div>
  <div class="partner" style="left:766px" role="img" aria-label="Partner charity badge"></div>
  <div class="abs footer-bottom">
    <div class="abs" style="left:62px;top:10px">Copyright © 2016 Dr. Marla J. Kalvoric. All Rights Reserved.</div>
    <div class="social" style="left:730px"><i></i>Friendora</div>
    <div class="social" style="left:794px"><i></i>Chirply</div>
  </div>
</footer>

</body>
</html>
```